Every Shelf Set Neatly or ESN Organized needs a business card design. ESN Organized is a professi

We need a business card design that is clean, sharp and conveys a sense of organization. I already have a logo.

Target Market(s)

Families (specifically mothers), small business owners, parents, seniors

Industry/Entity Type

Business

Contact Information for Business Card

My website is www.esnorganized-example.com and my Facebook page is http://www.sociallink-example.com/everyshelfsetneatly. The phone number is 418-552-7094 and I want to be listed as Lorna M. Pelham, Owner

Requirements
Must have
• My logo.

```html
<!DOCTYPE html>
<html lang="en">
<head>
<meta charset="utf-8">
<title>ESN Organized – Business Card</title>
<link rel="stylesheet" href="https://fonts.googleapis.com/css2?family=Open+Sans:ital,wght@0,400;0,600;1,400&display=swap">
<style>
  :root {
    --page-bg: #ecebe8;
    --card-bg: #ffffff;
    --brand-blue: #2f7fc4;
    --ink: #2b2b2b;
    --rule-blue: #5b9fd6;
    --card-shadow: rgba(0, 0, 0, 0.18);
  }
  * { box-sizing: border-box; margin: 0; padding: 0; }
  html, body {
    width: 1200px;
    height: 1200px;
    overflow: hidden;
    background: var(--page-bg);
    font-family: "Open Sans", sans-serif;
  }
  .canvas {
    position: relative;
    width: 1200px;
    height: 1200px;
    display: flex;
    align-items: center;
    justify-content: center;
  }
  .business-card {
    position: relative;
    width: 1000px;
    height: 571px;
    background: var(--card-bg);
    box-shadow: 0 6px 24px var(--card-shadow);
    color: var(--ink);
  }
  .brand {
    position: absolute;
    left: 52px;
    top: 58px;
    display: flex;
    flex-direction: column;
  }
  .brand-name {
    display: flex;
    align-items: center;
    gap: 18px;
    font-size: 62px;
    font-weight: 400;
    letter-spacing: 2px;
    color: var(--brand-blue);
    line-height: 1;
  }
  .brand-dot {
    width: 26px;
    height: 26px;
    border-radius: 50%;
    background: var(--brand-blue);
  }
  .website {
    display: flex;
    align-items: center;
    gap: 8px;
    margin: 20px 0 0 44px;
    font-size: 26px;
    letter-spacing: 0.5px;
  }
  .icon { width: 26px; height: 26px; flex: none; }
  .clip-area {
    position: absolute;
    right: 92px;
    top: 0;
    width: 48px;
    height: 160px;
    border-radius: 0 0 24px 24px;
    background: linear-gradient(180deg, #3d8ad0, #2f7fc4);
    opacity: 0.85;
  }
  .person {
    position: absolute;
    left: 56px;
    top: 268px;
  }
  .person-name {
    font-size: 44px;
    font-weight: 400;
    color: var(--brand-blue);
    line-height: 1.1;
  }
  .person-title {
    font-size: 26px;
    letter-spacing: 1px;
    margin-top: 4px;
  }
  .contact-line {
    position: absolute;
    left: 56px;
    top: 398px;
    display: flex;
    align-items: center;
    gap: 10px;
    font-size: 26px;
    letter-spacing: 0.8px;
  }
  .contact-divider { margin: 0 4px; }
  .social-square {
    width: 22px;
    height: 22px;
    background: var(--brand-blue);
    border-radius: 3px;
  }
  .rule {
    position: absolute;
    left: 56px;
    top: 446px;
    width: 810px;
    height: 2px;
    background: var(--rule-blue);
  }
  .tagline {
    position: absolute;
    left: 56px;
    top: 458px;
    font-size: 27px;
    font-style: italic;
    letter-spacing: 0.8px;
  }
</style>
</head>
<body>
<main class="canvas">
  <section class="business-card">
    <header class="brand">
      <div class="brand-name"><span>ESN Organized</span><span class="brand-dot"></span></div>
      <div class="website">
        <svg class="icon" viewBox="0 0 24 24" aria-hidden="true">
          <circle cx="12" cy="12" r="10" fill="none" stroke="#2f7fc4" stroke-width="2"/>
          <ellipse cx="12" cy="12" rx="4.5" ry="10" fill="none" stroke="#2f7fc4" stroke-width="1.6"/>
          <line x1="2" y1="12" x2="22" y2="12" stroke="#2f7fc4" stroke-width="1.6"/>
        </svg>
        <span>www.esnorganized-example.com</span>
      </div>
    </header>

    <div class="clip-area" role="img" aria-label="Blue paper clip holding the top edge of the card"></div>

    <div class="person">
      <h1 class="person-name">Lorna M. Pelham</h1>
      <p class="person-title">Owner</p>
    </div>

    <div class="contact-line">
      <svg class="icon" viewBox="0 0 24 24" aria-hidden="true">
        <rect x="3" y="6" width="18" height="14" rx="2" fill="none" stroke="#2f7fc4" stroke-width="2"/>
        <rect x="6" y="3" width="5" height="17" rx="1" fill="#2f7fc4"/>
        <rect x="13" y="9" width="5" height="2" fill="#2f7fc4"/>
        <rect x="13" y="13" width="5" height="2" fill="#2f7fc4"/>
      </svg>
      <span>418-552-7094</span>
      <span class="contact-divider">|</span>
      <span class="social-square"></span>
      <span>everyshelfsetneatly</span>
    </div>

    <div class="rule"></div>
    <p class="tagline">Every space sorted simply, and every shelf set neatly</p>
  </section>
</main>
</body>
</html>
```